Coastline Premier Retreats Business Card Design

Design a business card for Coastline Premier Retreats. Look at the website for colors and reference. Card should have logo, name, title, office number, mobile number, email, URL and a tagline like, "Luxury Hotel & Resort Email Marketing" (This might change).

https://www.coastlinepremierretreats.example

The rest I will leave up to your imagination.

Contact Information for Business Card

Logo, name, title, office number, mobile number, email, URL and a tagline like, "Luxury Hotel & Resort Email Marketing" (This might change).

```html
<!DOCTYPE html>
<html lang="en">
<head>
<meta charset="UTF-8">
<title>Coastline Premier Retreats Business Card</title>
<link href="https://fonts.googleapis.com/css2?family=Montserrat:wght@400;500;700&display=swap" rel="stylesheet">
<style>
  :root {
    --bg: #d2d6d7;
    --paper: #fbfbfa;
    --orange: #e66f16;
    --ink: #1d1d1d;
    --grey: #4a4a4a;
    --band: #161616;
    --emboss: #f4f1ec;
  }
  * { box-sizing: border-box; margin: 0; padding: 0; }
  html, body { width: 1200px; height: 829px; overflow: hidden; }
  body {
    background: var(--bg);
    font-family: "Montserrat", sans-serif;
    position: relative;
  }
  .card {
    position: absolute;
    top: 263px;
    width: 530px;
    height: 303px;
    overflow: hidden;
  }
  .card-front { left: 50px; background: var(--paper); }
  .card-back { left: 620px; background: var(--orange); display: flex; align-items: center; justify-content: center; }

  .person-name {
    position: absolute; left: 40px; top: 48px;
    color: var(--orange); font-weight: 700; font-size: 23px; letter-spacing: 1px;
    line-height: 28px; white-space: nowrap;
  }
  .person-title {
    position: absolute; left: 40px; top: 79px;
    color: var(--grey); font-size: 11px;
  }
  .divider {
    position: absolute; left: 36px; top: 100px; width: 450px; height: 1px;
    background: var(--orange);
  }
  .contact-list {
    position: absolute; left: 40px; top: 114px; list-style: none;
  }
  .contact-list li {
    display: flex; align-items: center; gap: 8px;
    font-size: 11px; color: var(--grey); line-height: 17px;
  }
  .contact-list svg { width: 9px; height: 9px; fill: var(--orange); flex: none; }

  .brand {
    position: absolute; right: 40px; top: 50px;
    display: flex; align-items: center; gap: 10px;
  }
  .brand-mark { width: 12px; height: 12px; background: var(--orange); flex: none; }
  .brand-name {
    font-weight: 700; font-size: 14px; line-height: 18px; color: var(--ink);
    letter-spacing: 1.5px; text-transform: uppercase;
  }
  .brand-name span { display: block; }

  .address {
    position: absolute; right: 40px; top: 200px; text-align: right;
    font-size: 11px; color: var(--grey); line-height: 16px;
  }
  .band { position: absolute; left: 0; bottom: 0; width: 530px; height: 70px; }
  .tagline {
    position: absolute; left: 0; right: 0; bottom: 14px; text-align: center;
    color: #fff; font-size: 11px; letter-spacing: 0.5px;
  }

  .back-brand { display: flex; align-items: center; gap: 12px; }
  .back-brand .brand-mark { width: 18px; height: 18px; background: var(--emboss); }
  .back-brand .brand-name { color: var(--emboss); font-size: 22px; line-height: 28px; letter-spacing: 2.5px; white-space: nowrap; }
</style>
</head>
<body>
  <section class="card card-front">
    <div class="brand">
      <span class="brand-mark"></span>
      <span class="brand-name"><span>Coastline</span><span>Premier Retreats</span></span>
    </div>

    <h1 class="person-name">DANIEL REYES</h1>
    <p class="person-title">CEO/Founder</p>
    <div class="divider"></div>

    <ul class="contact-list">
      <li><svg viewBox="0 0 10 10"><rect x="2.5" y="0" width="5" height="10" rx="1"/></svg>555.014.2300</li>
      <li><svg viewBox="0 0 10 10"><path d="M0 4h10v6H0zM2 1h6v2H2z"/></svg>+34 600 555 014</li>
      <li><svg viewBox="0 0 10 10"><path d="M0 2h10v7H0zM0 2l5 4 5-4"/></svg>info@coastlinepremierretreats.example</li>
      <li><svg viewBox="0 0 10 10"><circle cx="5" cy="5" r="5"/></svg>www.coastlinepremierretreats.example</li>
    </ul>

    <p class="address">PO Box 48, 210 Harbor Rd<br>Seaside, CA 90210</p>

    <svg class="band" viewBox="0 0 530 70" preserveAspectRatio="none">
      <path d="M0 36 H120 Q135 36 140 31 L146 25 Q151 20 166 20 H364 Q379 20 384 25 L390 31 Q395 36 410 36 H530" fill="none" stroke="var(--orange)" stroke-width="1.5" transform="translate(0,-8)"/>
      <path d="M0 40 H120 Q135 40 140 34 L146 27 Q151 22 166 22 H364 Q379 22 384 27 L390 34 Q395 40 410 40 H530 V70 H0 Z" fill="var(--band)"/>
    </svg>
    <p class="tagline">Luxury Hotel &amp; Resort Email Marketing</p>
  </section>

  <section class="card card-back">
    <div class="back-brand">
      <span class="brand-mark"></span>
      <span class="brand-name">Coastline Premier Retreats</span>
    </div>
  </section>
</body>
</html>
```